Letterhead for Conveyancing Company

Use existing logo to create a letterhead for a conveyancing company. Must be able to be used in Microsoft Word. Easy to read and professional.
Contact information to be at the bottom.
Bright Oak Conveyancing Pty Ltd
ACN 621 984 736PO Box 535 Campbelltown SA 5074
Mobile - 0461739286
Web address - www.brightoakconveyancing.com.au

Requirements
Must have
• Logo and contact details.
• Simple and professional.

```html
<!DOCTYPE html>
<html lang="en">
<head>
<meta charset="utf-8">
<title>Bright Oak Conveyancing – Letterhead</title>
<link rel="stylesheet" href="https://fonts.googleapis.com/css2?family=Arimo:wght@400;700&display=swap">
<style>
  :root {
    --backdrop: #d9dbdc;
    --paper: #ffffff;
    --brand-pink: #e0449a;
    --brand-pink-deep: #cf2f87;
    --brand-grey: #8a8a8a;
    --swoosh-grey: #c4c6c8;
    --body-text: #6a6a6a;
    --signature-tone: #eeeeee;
  }
  * { box-sizing: border-box; margin: 0; padding: 0; }
  html, body {
    width: 1200px; height: 784px; overflow: hidden;
    background: var(--backdrop);
    font-family: "Arimo", Arial, sans-serif;
  }
  .letterhead {
    position: absolute; left: 335px; top: 17px;
    width: 530px; height: 750px;
    background: var(--paper);
    box-shadow: 0 2px 10px rgba(0,0,0,0.12);
    overflow: hidden;
  }
  .rule-top {
    position: absolute; left: 0; top: 30px;
    width: 318px; height: 5px; background: var(--brand-pink);
  }
  .rule-side {
    position: absolute; right: 0; top: 104px;
    width: 62px; height: 5px; background: var(--brand-grey);
  }
  .brand {
    position: absolute; left: 328px; top: 28px;
    width: 140px; color: var(--brand-pink);
    font-weight: 700; text-transform: uppercase; line-height: 1;
  }
  .brand-name { display: block; font-size: 29px; letter-spacing: -0.5px; }
  .brand-sub { display: block; font-size: 11.5px; letter-spacing: 2.4px; margin-top: 6px; }
  .letter-body {
    position: absolute; left: 62px; top: 140px; width: 405px;
    color: var(--body-text); font-size: 9.6px; line-height: 1.38;
  }
  .letter-body p + p { margin-top: 12px; }
  .signature {
    position: absolute; left: 80px; top: 470px;
    width: 160px; height: 56px;
    background: var(--signature-tone); border-radius: 4px;
  }
  .footer-wave { position: absolute; left: 0; bottom: 0; width: 530px; height: 190px; }
  .contact {
    position: absolute; left: 16px; bottom: 12px;
    color: #fff; font-size: 7.4px; line-height: 11.5px;
  }
  .contact-icons { display: flex; gap: 5px; margin-bottom: 2px; }
  .contact-icons svg { width: 9px; height: 9px; }
  .sep { opacity: 0.7; padding: 0 3px; }
</style>
</head>
<body>
  <main class="letterhead">
    <div class="rule-top"></div>
    <div class="brand">
      <span class="brand-name">Bright Oak</span>
      <span class="brand-sub">Conveyancing</span>
    </div>
    <div class="rule-side"></div>

    <section class="letter-body">
      <p>Lorem Ipsum is simply dummy text of the printing and typesetting industry. Lorem Ipsum has been the industry's standard dummy text ever since the 1500s, when an unknown printer took a galley of type and scrambled it to make a type specimen book. It has survived not only five centuries, but also the leap into electronic typesetting, remaining essentially unchanged. It was popularised in the 1960s with the release of Typeflex sheets containing Lorem Ipsum passages, and more recently with desktop publishing software like LayoutForge including versions of Lorem Ipsum.</p>
      <p>It is a long established fact that a reader will be distracted by the readable content of a page when looking at its layout. The point of using Lorem Ipsum is that it has a more-or-less normal distribution of letters, as opposed to using 'Content here, content here', making it look like readable English. Many desktop publishing packages and web page editors now use Lorem Ipsum as their default model text, and a search for 'lorem ipsum' will uncover many web sites still in their infancy. Various versions have evolved over the years, sometimes by accident, sometimes on purpose (injected humour and the like).</p>
      <p>Contrary to popular belief, Lorem Ipsum is not simply random text. It has roots in a piece of classical Latin literature from 45 BC, making it over 2000 years old. Edwin Harlow, a Latin professor at Fenwick College in Ashvale, looked up one of the more obscure Latin words, consectetur, from a Lorem Ipsum passage, and going through the cites of the word in classical literature, discovered the undoubtable source. Lorem Ipsum comes from sections 1.10.32 and 1.10.33 of "de Finibus Bonorum et Malorum" structures, to generate Lorem Ipsum which looks reasonable. The generated Lorem Ipsum is therefore always free from repetition, injected humour, or non-characteristic words etc.</p>
    </section>

    <div class="signature" role="img" aria-label="Handwritten signature"></div>

    <svg class="footer-wave" viewBox="0 0 530 190" preserveAspectRatio="none" aria-hidden="true">
      <defs>
        <linearGradient id="pinkBand" x1="0" y1="0" x2="1" y2="0">
          <stop offset="0" stop-color="var(--brand-pink-deep)"/>
          <stop offset="1" stop-color="var(--brand-pink)"/>
        </linearGradient>
      </defs>
      <path d="M0,0 C140,8 220,120 530,158 L530,190 L0,190 Z" fill="var(--swoosh-grey)"/>
      <path d="M0,18 C130,28 210,132 530,170 L530,190 L0,190 Z" fill="url(#pinkBand)"/>
    </svg>

    <div class="contact">
      <div class="contact-icons">
        <svg viewBox="0 0 10 10"><circle cx="5" cy="5" r="4.5" fill="#fff"/><path d="M5 2.3a1.9 1.9 0 0 1 1.9 1.9C6.9 5.6 5 7.8 5 7.8S3.1 5.6 3.1 4.2A1.9 1.9 0 0 1 5 2.3z" fill="var(--brand-pink)"/></svg>
        <svg viewBox="0 0 10 10"><circle cx="5" cy="5" r="4.5" fill="#fff"/><rect x="3.6" y="2.4" width="2.8" height="5.2" rx="0.5" fill="var(--brand-pink)"/></svg>
        <svg viewBox="0 0 10 10"><circle cx="5" cy="5" r="4.5" fill="#fff"/><rect x="2.6" y="3.3" width="4.8" height="3.4" fill="var(--brand-pink)"/></svg>
        <svg viewBox="0 0 10 10"><circle cx="5" cy="5" r="4.5" fill="#fff"/><circle cx="5" cy="5" r="2.2" fill="none" stroke="var(--brand-pink)" stroke-width="1"/></svg>
      </div>
      <div><strong>PO Box 871 Marlowdale SA 5096</strong></div>
      <div>ACN 583 217 469<span class="sep">|</span>0461739286</div>
      <div>contact@brightoakconveyancing.com.au<span class="sep">|</span>www.brightoakconveyancing.com.au</div>
    </div>
  </main>
</body>
</html>
```